Corvane Holdings , new business card design

investment firm with corporate clients . need double sided business card , vertical and horizontal options ,logo must be clear. prefer pantone colors only and sharp design. website also www.corvane.ae

Khalid Bin Tarrafi
Managing Director
Tel. +971 4 387 2940
Mobile +971 50 518 2403
khalid@corvane.ae
Q-Span Plaza, officw 18-B07, Warqa Gardens, Dubai

Contact Information for Business Card

Khalid Bin Tarrafi
Managing Director

Font styles to use
Serif

Colors

Designer to choose colors to be used in the design.

```html
<!DOCTYPE html>
<html lang="en">
<head>
<meta charset="utf-8">
<title>Corvane Holdings — Business Card</title>
<link href="https://fonts.googleapis.com/css2?family=Roboto:wght@300;400;500;700&display=swap" rel="stylesheet">
<style>
  :root {
    --backdrop: #dcdcdc;
    --paper: #f7f7f7;
    --brand-blue: #436d92;
    --ink: #111111;
    --text-grey: #4d4d4d;
    --white: #ffffff;
  }
  * { margin: 0; padding: 0; box-sizing: border-box; }
  html, body {
    width: 1200px;
    height: 960px;
    overflow: hidden;
    background: var(--backdrop);
    font-family: "Roboto", Arial, sans-serif;
  }
  .canvas { position: relative; width: 1200px; height: 960px; }

  .card { position: absolute; }
  .card--front {
    left: 314px; top: 113px; width: 574px; height: 342px;
    background: var(--paper);
  }
  .card--back {
    left: 311px; top: 472px; width: 600px; height: 343px;
    background: var(--brand-blue);
  }

  .wordmark {
    position: absolute;
    text-align: right;
    font-weight: 300;
    line-height: 1;
    white-space: nowrap;
  }
  .wordmark__name { display: block; font-size: 40px; letter-spacing: 19px; margin-right: -19px; }
  .wordmark__sub { display: block; font-size: 12px; letter-spacing: 14.6px; margin-right: -14.6px; margin-top: 6px; }
  .card--front .wordmark { right: 12px; top: 46px; color: var(--ink); }
  .card--back .wordmark { right: 43px; top: 233px; color: var(--white); }

  .holder { position: absolute; left: 36px; top: 184px; }
  .holder__name {
    font-size: 20px; font-weight: 700; color: var(--brand-blue);
    letter-spacing: -0.2px; line-height: 24px;
  }
  .holder__title {
    font-size: 14px; font-weight: 500; color: var(--ink);
    line-height: 18px; margin-top: 2px;
  }

  .divider {
    position: absolute; left: 36px; top: 237px; width: 526px; height: 3px;
    display: flex; gap: 3px;
  }
  .divider span { flex: 1; background: var(--brand-blue); }

  .contact {
    position: absolute; left: 35px; top: 252px;
    font-size: 14px; color: var(--text-grey); line-height: 21px;
  }
  .contact__row { display: flex; align-items: center; white-space: nowrap; }
  .contact__item { display: inline-flex; align-items: center; margin-right: 8px; }
  .contact__icon { width: 13px; height: 13px; margin-right: 5px; fill: var(--brand-blue); }

  .back-url {
    position: absolute; right: 43px; top: 289px;
    color: var(--white); font-size: 15px; font-weight: 400;
    letter-spacing: 5.4px; margin-right: -5.4px;
  }
</style>
</head>
<body>
<main class="canvas">

  <section class="card card--front" aria-label="Business card front">
    <div class="wordmark">
      <span class="wordmark__name">CORVANE</span>
      <span class="wordmark__sub">HOLDINGS</span>
    </div>

    <div class="holder">
      <p class="holder__name">KHALID BIN TARRAFI</p>
      <p class="holder__title">MANAGING DIRECTOR</p>
    </div>

    <div class="divider" aria-hidden="true"><span></span><span></span><span></span></div>

    <div class="contact">
      <p class="contact__row">Q-Span Plaza, officw 18-B07, Warqa Gardens, Dubai</p>
      <p class="contact__row">
        <span class="contact__item">
          <svg class="contact__icon" viewBox="0 0 24 24" aria-hidden="true"><path d="M6.6 10.8c1.4 2.8 3.8 5.1 6.6 6.6l2.2-2.2c.3-.3.7-.4 1-.2 1.1.4 2.3.6 3.6.6.6 0 1 .4 1 1V20c0 .6-.4 1-1 1C10.6 21 3 13.4 3 4c0-.6.4-1 1-1h3.5c.6 0 1 .4 1 1 0 1.3.2 2.5.6 3.6.1.3 0 .7-.2 1L6.6 10.8z"/></svg>
          +971 4 387 2940
        </span>
        <span class="contact__item">
          <svg class="contact__icon" viewBox="0 0 24 24" aria-hidden="true"><path d="M7 1h10a2 2 0 0 1 2 2v18a2 2 0 0 1-2 2H7a2 2 0 0 1-2-2V3a2 2 0 0 1 2-2zm0 3v14h10V4H7zm5 15.2a1.2 1.2 0 1 0 0 2.4 1.2 1.2 0 0 0 0-2.4z"/></svg>
          +971 50 518 2403
        </span>
        <span class="contact__item">
          <svg class="contact__icon" viewBox="0 0 24 24" aria-hidden="true"><path d="M2 5h20v14H2V5zm2 2v.4l8 5.2 8-5.2V7H4zm0 2.8V17h16V9.8l-8 5.2-8-5.2z"/></svg>
          khalid@corvane.ae
        </span>
      </p>
      <p class="contact__row">
        <span class="contact__item">
          <svg class="contact__icon" viewBox="0 0 24 24" aria-hidden="true"><path d="M12 2a10 10 0 1 0 0 20 10 10 0 0 0 0-20zm-1 17.9A8 8 0 0 1 4.2 10.8L9 15.6v1c0 1.1.9 2 2 2v1.3zm6.9-2.5c-.3-.8-1-1.4-1.9-1.4h-1v-3c0-.6-.4-1-1-1H8v-2h2c.6 0 1-.4 1-1V7h2c1.1 0 2-.9 2-2v-.4a8 8 0 0 1 2.9 12.8z"/></svg>
          www.corvane.ae
        </span>
      </p>
    </div>
  </section>

  <section class="card card--back" aria-label="Business card back">
    <div class="wordmark">
      <span class="wordmark__name">CORVANE</span>
      <span class="wordmark__sub">HOLDINGS</span>
    </div>
    <p class="back-url">www.corvane.ae</p>
  </section>

</main>
</body>
</html>
```